Medical Billing Company Needs a Business Card Design

We need a business card design for a Florida based medical billing company called 'Clinicians Keystone Solutions'. We specialize in providing revenue cycle management services to physician and therapist offices (we're basically their back-office processing partner for providing billing software, claims submissions, A/R follow-up and patient statements & collections. Our logo is red and blue-ish, so make sure that whatever other elements are used will match appropriately. Our current business card design has a too small font size. I'd like to project an image that shows we are modern & reliable. On a side note, I'm planning on using ZUB for printing these cards.

Target Market(s)

Office managers, physicians, therapists

Industry/Entity Type

Printing

Requirements
Must have
• Logo
Name of Employee
Phone
Fax
E-mail
Website

```html
<!DOCTYPE html>
<html lang="en">
<head>
<meta charset="utf-8">
<title>Clinicians Keystone – Business Card</title>
<link rel="stylesheet" href="https://fonts.googleapis.com/css2?family=PT+Sans:wght@400;700&display=swap">
<style>
  :root {
    --page: #f3ede3;
    --card-light: #ecd7b0;
    --card-light-2: #e2c897;
    --navy: #27235f;
    --red: #9e1b22;
    --white: #ffffff;
    --font: "PT Sans", sans-serif;
  }
  * { box-sizing: border-box; margin: 0; padding: 0; }
  html, body { width: 1200px; height: 1106px; overflow: hidden; }
  body { background: var(--page); font-family: var(--font); position: relative; }

  .card {
    position: absolute; width: 610px; height: 350px;
    border-radius: 22px; overflow: hidden;
    background: linear-gradient(160deg, var(--card-light), var(--card-light-2));
    box-shadow: 0 6px 18px rgba(0,0,0,.18);
  }
  .card--front { left: 182px; top: 147px; }
  .card--back  { left: 288px; top: 611px; }
  .card__shapes { position: absolute; inset: 0; width: 100%; height: 100%; }

  .brand {
    position: absolute; left: 0; right: 0; top: 58px;
    display: flex; justify-content: center; align-items: center; gap: 12px;
    color: var(--navy); font-size: 29px; font-weight: 400; letter-spacing: 2px;
  }
  .brand__square { width: 18px; height: 18px; background: var(--red); }
  .brand--mirrored { transform: scaleX(-1); }

  .holder {
    position: absolute; right: 346px; top: 247px; text-align: right; color: var(--white);
  }
  .holder__name { font-size: 20px; font-weight: 700; line-height: 24px; }
  .holder__title { font-size: 15px; line-height: 20px; margin-bottom: 8px; }
  .holder__address { font-size: 15px; line-height: 22px; }

  .divider {
    position: absolute; left: 277px; top: 252px; width: 1px; height: 82px; background: rgba(255,255,255,.7);
  }

  .contacts { position: absolute; left: 293px; top: 249px; list-style: none; color: var(--white); }
  .contacts li { display: flex; align-items: center; gap: 7px; font-size: 15px; line-height: 23px; }
  .contacts svg { width: 13px; height: 13px; fill: var(--white); flex: none; }

  .website {
    position: absolute; left: 0; right: 0; top: 286px; text-align: center;
    color: var(--white); font-size: 23px; letter-spacing: 2px;
  }
</style>
</head>
<body>

<section class="card card--front" aria-label="Business card front">
  <svg class="card__shapes" viewBox="0 0 610 350" preserveAspectRatio="none" aria-hidden="true">
    <path d="M0,104 Q250,238 500,205 Q250,222 0,138 Z" fill="var(--red)"/>
    <path d="M0,148 Q290,265 610,156 L610,350 L0,350 Z" fill="var(--navy)"/>
  </svg>

  <div class="brand"><span class="brand__square"></span><span>CLINICIANS KEYSTONE</span></div>

  <div class="holder">
    <p class="holder__name">Your Name</p>
    <p class="holder__title">Title</p>
    <p class="holder__address">Street Name, City Name<br>State Zip Code</p>
  </div>
  <div class="divider"></div>

  <ul class="contacts">
    <li><svg viewBox="0 0 16 16"><path d="M3 1l3 3-2 2c1 2 3 4 5 5l2-2 3 3-2 3C6 15 1 10 1 3z"/></svg>123-456-0789</li>
    <li><svg viewBox="0 0 16 16"><path d="M4 0h8v16H4zM5.5 2v9h5V2zM7 13h2v1.5H7z"/></svg>123-456-0789</li>
    <li><svg viewBox="0 0 16 16"><path d="M1 6l7-5 7 5v9H1zM2.5 7l5.5 4 5.5-4z"/></svg>info@cliniciankeystone.com</li>
    <li><svg viewBox="0 0 16 16"><path d="M8 0a8 8 0 100 16A8 8 0 008 0zm-1 2v3H4.5A6 6 0 017 2zm2 0a6 6 0 012.5 3H9zM2.3 7H7v2H2.3zm6.7 0h4.7v2H9zM4.5 11H7v3a6 6 0 01-2.5-3zm4.5 0h2.5A6 6 0 019 14z"/></svg>www.cliniciankeystone.com</li>
  </ul>
</section>

<section class="card card--back" aria-label="Business card back">
  <svg class="card__shapes" viewBox="0 0 610 350" preserveAspectRatio="none" aria-hidden="true">
    <path d="M610,108 Q360,240 110,228 Q360,232 610,146 Z" fill="var(--red)"/>
    <path d="M0,162 Q300,290 610,152 L610,350 L0,350 Z" fill="var(--navy)"/>
  </svg>

  <div class="brand brand--mirrored"><span class="brand__square"></span><span>CLINICIANS KEYSTONE</span></div>

  <p class="website">www.cliniciankeystone.com</p>
</section>

</body>
</html>
```